Business Card Design

New business card design

Target Market(s)

Residential & Commercial Property Managers

Industry/Entity Type

Plumbing Services

Contact Information for Business Card

Name - Rowan Keddle, title - Director, Phone Number - 0431 286 517, email - rowan@tbk-plumbing.com.au, Company ABN - 73 215 904 386,

Font styles to use
Sans Serif

Colors
0054AA
0677BA
7BADD7
CADEEF
E8F1F8

```html
<!DOCTYPE html>
<html lang="en">
<head>
<meta charset="utf-8">
<title>TBK Plumbing Services – Business Card</title>
<link rel="stylesheet" href="https://fonts.googleapis.com/css2?family=Montserrat:wght@400;500;700&display=swap">
<style>
  :root {
    --backdrop: #d9d8d5;
    --card-dark: #1d242c;
    --card-light: #ffffff;
    --accent-blue: #2aa3dd;
    --ink-light: #ffffff;
    --ink-dark: #1d242c;
  }
  * { box-sizing: border-box; margin: 0; padding: 0; }
  html, body {
    width: 1200px; height: 801px; overflow: hidden;
    background: var(--backdrop);
    font-family: "Montserrat", sans-serif;
  }
  .canvas {
    position: relative; width: 1200px; height: 801px;
    display: flex; align-items: center; justify-content: center; gap: 50px;
  }
  .card {
    width: 520px; height: 318px; position: relative; overflow: hidden;
    box-shadow: 0 10px 24px rgba(0,0,0,0.18);
  }

  /* Contact side */
  .card--contact { display: flex; }
  .card__brand-panel {
    width: 46%; background: var(--card-light);
    display: flex; align-items: center; justify-content: center;
    padding: 0 24px;
  }
  .card__details-panel {
    flex: 1; background: var(--card-dark); color: var(--ink-light);
    padding: 62px 0 0 34px;
  }

  .company-name {
    font-weight: 500; line-height: 1.25; text-align: center;
  }
  .company-name--small { font-size: 20px; color: var(--ink-dark); max-width: 170px; }
  .company-name--large { font-size: 40px; color: var(--ink-light); max-width: 400px; }

  .person__name { color: var(--accent-blue); font-weight: 700; font-size: 20px; }
  .person__title { font-size: 13px; margin-top: 2px; }
  .divider { color: var(--accent-blue); font-size: 12px; margin: 10px 0 6px; }
  .details__abn { font-size: 12px; }
  .details__abn-label { color: var(--accent-blue); }
  .contact-list { list-style: none; font-size: 13px; }
  .contact-list li { display: flex; align-items: center; gap: 8px; margin-bottom: 5px; white-space: nowrap; }
  .contact-list svg { width: 12px; height: 12px; flex: none; }

  /* Brand side */
  .card--brand {
    background: var(--card-dark);
    display: flex; align-items: center; justify-content: center;
  }
</style>
</head>
<body>
<main class="canvas">
  <section class="card card--contact" aria-label="Business card, contact side">
    <div class="card__brand-panel">
      <p class="company-name company-name--small">TBK Plumbing Services</p>
    </div>
    <div class="card__details-panel">
      <p class="person__name">Rowan Keddle</p>
      <p class="person__title">Director</p>
      <p class="divider">/</p>
      <p class="details__abn"><span class="details__abn-label">ABN</span> - 73 215 904 386</p>
      <p class="divider">/</p>
      <ul class="contact-list">
        <li>
          <svg viewBox="0 0 12 12" aria-hidden="true"><path fill="#2aa3dd" d="M2.5 1l2 2.2-1 1.2a7 7 0 0 0 4 4l1.2-1 2.2 2-1.3 1.6C5 11 1 7 .9 2.3z"/></svg>
          0431 286 517
        </li>
        <li>
          <svg viewBox="0 0 12 12" aria-hidden="true"><rect x="0.5" y="2" width="11" height="8" fill="#2aa3dd"/><path d="M0.5 2l5.5 4.5L11.5 2" fill="none" stroke="#1d242c" stroke-width="1"/></svg>
          rowan@tbk-plumbing.com.au
        </li>
      </ul>
    </div>
  </section>

  <section class="card card--brand" aria-label="Business card, brand side">
    <p class="company-name company-name--large">TBK Plumbing Services</p>
  </section>
</main>
</body>
</html>
```